Kestrel Facilities Business Card Design

We would now like to design business cards with the new Kestrel Facilities logo

Target Market(s)

Professional

Industry/Entity Type

Professional services

Contact Information for Business Card

Employee name, title, phone number, email address, corporate office address and logo.

Font styles to use
Sans Serif

Colors
0054AA
0677BA
7BADD7
CADEEF
E8F1F8

Requirements
Must have
• My logo
Should not have
• any other pictures or images besides my logo

```html
<!DOCTYPE html>
<html lang="en">
<head>
<meta charset="utf-8">
<title>Kestrel Facilities – Business Card</title>
<link href="https://fonts.googleapis.com/css2?family=Montserrat:wght@400;500;600;800&display=swap" rel="stylesheet">
<style>
  :root {
    --stage: #2a2a2a;
    --brand-blue: #3375bd;
    --brand-deep: #0054aa;
    --swoosh-grey: #a9a9ab;
    --paper: #ffffff;
    --ink: #1e1e1e;
  }
  * { box-sizing: border-box; margin: 0; padding: 0; }
  html, body {
    width: 1200px; height: 960px; overflow: hidden;
    background: var(--stage);
    font-family: "Montserrat", sans-serif;
  }
  .stage {
    width: 1200px; height: 960px;
    display: flex; flex-direction: column;
    align-items: center; justify-content: center; gap: 40px;
  }
  .card {
    position: relative;
    width: 700px; height: 400px;
    border-radius: 22px;
    overflow: hidden;
  }
  .card--front { background: var(--brand-blue); display: flex; align-items: center; justify-content: center; }
  .card--back { background: var(--paper); }

  .wordmark { display: flex; align-items: center; gap: 16px; font-weight: 600; letter-spacing: .5px; line-height: 1.05; }
  .wordmark__square { width: 40px; height: 40px; flex: none; }
  .card--front .wordmark { color: var(--paper); font-size: 46px; }
  .card--front .wordmark__square { background: var(--paper); width: 52px; height: 52px; }
  .card--back .wordmark { position: absolute; left: 52px; top: 128px; color: var(--brand-blue); font-size: 30px; }
  .card--back .wordmark__square { background: var(--brand-blue); }

  .divider { position: absolute; left: 338px; top: 80px; width: 2px; height: 175px; background: var(--brand-blue); }

  .contact { position: absolute; left: 370px; top: 78px; color: var(--ink); }
  .contact__name { color: var(--brand-blue); font-weight: 800; font-size: 22px; text-transform: uppercase; letter-spacing: .3px; }
  .contact__title { font-size: 15px; font-weight: 500; margin-top: 2px; }
  .contact__address { font-size: 14.5px; line-height: 1.35; margin-top: 16px; }
  .contact__lines { list-style: none; margin-top: 14px; font-size: 14.5px; line-height: 1.55; }
  .contact__lines li { display: flex; align-items: center; gap: 10px; }
  .contact__icon { width: 15px; height: 15px; fill: var(--brand-blue); flex: none; }

  .wave { position: absolute; inset: 0; width: 100%; height: 100%; }
  .wave__band { fill: var(--brand-blue); }
  .wave__swoosh { fill: var(--swoosh-grey); }
</style>
</head>
<body>
<main class="stage">
  <section class="card card--front" aria-label="Card front">
    <div class="wordmark"><span class="wordmark__square"></span><span>Kestrel<br>Facilities</span></div>
  </section>

  <section class="card card--back" aria-label="Card back">
    <svg class="wave" viewBox="0 0 700 400" aria-hidden="true">
      <path class="wave__swoosh" d="M500 252 C600 232 675 195 700 140 L700 160 C670 205 600 240 500 252 Z"/>
      <path class="wave__band" d="M150 400 C230 300 390 262 540 240 C630 226 685 190 700 168 L700 400 Z"/>
    </svg>

    <div class="wordmark"><span class="wordmark__square"></span><span>Kestrel<br>Facilities</span></div>
    <div class="divider"></div>

    <div class="contact">
      <h1 class="contact__name">Dara Whitlock</h1>
      <p class="contact__title">Co-Founder</p>
      <p class="contact__address">4180 N. Harbor Lane<br>Suite 210 Northgate.14</p>
      <ul class="contact__lines">
        <li>
          <svg class="contact__icon" viewBox="0 0 24 24"><path d="M6.6 10.8a15 15 0 0 0 6.6 6.6l2.2-2.2c.3-.3.7-.4 1-.2 1.1.4 2.3.6 3.6.6.6 0 1 .4 1 1V20c0 .6-.4 1-1 1A17 17 0 0 1 3 4c0-.6.4-1 1-1h3.5c.6 0 1 .4 1 1 0 1.3.2 2.5.6 3.6.1.3 0 .7-.2 1z"/></svg>
          +254-160-47213
        </li>
        <li>
          <svg class="contact__icon" viewBox="0 0 24 24"><path d="M2 5h20v14H2z M3.5 6.5 12 13l8.5-6.5" fill="none" stroke="#3375bd" stroke-width="2"/></svg>
          hello@kestrelfac.com
        </li>
      </ul>
    </div>
  </section>
</main>
</body>
</html>
```